Adelaide based cleaning and remediation business needs a website design

We are launching a new company with no clients as yet so we don't have the benefit of Plimora Reviews to build confidence. We can use our  past work history with other employers in the industry to give some credibility. Happy to use any colour scheme as long as it look interesting when people click on the site it gets there attention. enquiry . I have supplied a mock up the important information and various photos as they tell a lot of the story.

```html
<!DOCTYPE html>
<html lang="en">
<head>
<meta charset="utf-8">
<title>Korvane Services — Cleaning with Care, Dignity, and Experience</title>
<link href="https://fonts.googleapis.com/css2?family=Lato:ital,wght@0,400;0,700;0,900;1,400&display=swap" rel="stylesheet">
<style>
:root{
  --navy:#0f2a4a;
  --navy-deep:#0b2240;
  --green:#10c588;
  --ink:#1b2a3a;
  --text:#333b44;
  --sky:#e3f0fb;
  --white:#ffffff;
  --line:#8a939c;
}
*{box-sizing:border-box;margin:0;padding:0}
html,body{width:1200px;height:3563px;overflow:hidden;background:var(--white);font-family:"Lato",sans-serif;color:var(--text)}
.page{position:relative;width:1200px;height:3563px}
.abs{position:absolute}
.nav{position:absolute;left:0;top:0;width:1200px;height:86px;background:var(--white);z-index:3}
.nav a{position:absolute;top:34px;font-size:15px;color:var(--ink);text-decoration:none}
.nav a.active{color:var(--green);text-decoration:underline}
.nav .cta{top:20px;left:935px;width:153px;height:47px;border-radius:24px;background:var(--navy);color:var(--white);font-weight:700;font-size:17px;display:flex;align-items:center;justify-content:center}
.brand{position:absolute;left:501px;top:-29px;width:192px;height:192px;border-radius:50%;background:var(--white);z-index:4;display:flex;align-items:flex-end;justify-content:center;padding-bottom:48px;font-weight:900;font-size:22px;color:var(--navy)}
.hero{position:absolute;left:0;top:86px;width:1200px;height:513px;background:radial-gradient(ellipse at 40% 40%,#a7825a 0%,#6b4a30 40%,#2a1d14 100%)}
.hero h1{position:absolute;left:0;top:120px;width:1200px;text-align:center;color:var(--white);font-weight:700;font-size:54px;line-height:64px;text-shadow:0 3px 6px rgba(0,0,0,.5)}
.btn{position:absolute;background:var(--green);color:var(--white);font-weight:700;display:flex;align-items:center;justify-content:center;border-radius:24px}
.h2{position:absolute;font-weight:700;color:var(--ink)}
.about-text{position:absolute;left:110px;top:744px;width:445px;font-size:14.5px;line-height:26.6px;color:var(--text)}
.frame{position:absolute;left:637px;top:683px;width:452px;height:328px;border:2px solid var(--navy);border-radius:20px}
.photo{position:absolute}
.services{position:absolute;left:0;top:1134px;width:1200px;height:655px;background:var(--sky)}
.svc-label{position:absolute;width:340px;text-align:center;font-size:27px;line-height:39px;color:var(--ink)}
.field{position:absolute;left:644px;width:445px;border:1px solid var(--line);background:var(--white);font-size:15px;color:#555;padding-left:48px;display:flex;align-items:center}
.field svg{position:absolute;left:13px}
.info{position:absolute;left:152px;font-size:15px;color:var(--text);display:flex;align-items:center;gap:16px}
.info svg{flex:none}
.quote{position:absolute;left:0;top:2312px;width:1200px;height:391px;background:linear-gradient(180deg,rgba(28,53,94,.92),rgba(20,40,75,.95)),linear-gradient(90deg,#3d4a5e,#6b5a48,#2e3a4d)}
.quote p{position:absolute;left:0;width:1200px;text-align:center;color:var(--white);font-size:15px}
.card{position:absolute;top:2873px;width:389px;height:221px;background:var(--white);border-radius:10px;box-shadow:0 4px 18px rgba(0,0,0,.14);padding:24px 46px 0 70px}
.card q{display:block;font-style:italic;font-size:14.5px;line-height:26px;color:#555;quotes:none}
.card .who{position:absolute;left:70px;top:165px;font-size:15px;line-height:23px;color:var(--ink)}
.card .who b{font-weight:700}
.mark{position:absolute;font-size:64px;font-weight:900;color:#7fdcbc;line-height:1}
.avatar{position:absolute;width:92px;height:92px;border-radius:50%}
.footer{position:absolute;left:0;top:3187px;width:1200px;height:376px;background:var(--navy-deep)}
.fh{position:absolute;top:92px;font-size:22px;font-weight:700;color:var(--green)}
.flist{position:absolute;list-style:none;font-size:15px;color:var(--white)}
.flist li{height:32.5px;display:flex;align-items:center;gap:10px}
.dot{width:8px;height:8px;border-radius:50%;background:var(--green);flex:none}
</style>
</head>
<body>
<div class="page">

  <header class="nav">
    <a class="active" style="left:110px">Home</a>
    <a style="left:187px">About Us</a>
    <a style="left:285px">Services</a>
    <a style="left:377px">Pricing</a>
    <a style="left:734px">Teastimonials</a>
    <a style="left:862px">FAQs</a>
    <a class="cta">Contact Us</a>
  </header>
  <div class="brand">Korvane</div>

  <section class="hero" role="img" aria-label="Photo of cleaners in protective suits clearing a fire-damaged room">
    <h1>Cleaning with Care, Dignity,<br>and Experience</h1>
    <a class="btn" style="left:523px;top:282px;width:152px;height:44px;font-size:17px">Get Started</a>
  </section>

  <h2 class="h2" style="left:110px;top:670px;font-size:44px">About Us</h2>
  <p class="about-text">Adelaide-based Korvane Services is a family-run organisation.We have been in operation for more than two decades.We've gained some knowledge about cleaning and squalor removal services throughout the years.<br>As a small South Australian company, we base everything on responsibility honesty and fairness .We are aware of the confidence you put in us when you seek our help.</p>
  <a class="btn" style="left:112px;top:961px;width:152px;height:47px;font-size:17px">Read More</a>
  <div class="frame"></div>
  <div class="photo" role="img" aria-label="Photo of a fire-damaged kitchen with exposed ceiling insulation" style="left:650px;top:693px;width:428px;height:310px;border-radius:16px;background:linear-gradient(160deg,#6e5f58,#2c2622 55%,#8a8580)"></div>
  <div class="photo" role="img" aria-label="Photo of pigeons on a droppings-stained ledge" style="left:598px;top:906px;width:160px;height:144px;border-radius:18px;border:5px solid var(--white);background:linear-gradient(180deg,#c9d4dc,#e8e2d6 60%,#b7ab97)"></div>

  <section class="services">
    <h2 class="h2" style="left:0;width:1200px;text-align:center;top:72px;font-size:44px">Korvane Services</h2>
    <svg class="abs" style="left:0;top:0" width="1200" height="655" aria-hidden="true">
      <g fill="none" stroke="#10c588" stroke-width="9">
        <path d="M112.7 271 A152 152 0 1 0 413.3 271"/>
        <path d="M449 336 A152 152 0 1 1 747 336"/>
        <path d="M782.7 271 A152 152 0 1 0 1083.3 271"/>
      </g>
      <g fill="#10c588">
        <circle cx="112.7" cy="271" r="7"/><circle cx="413.3" cy="271" r="7"/>
        <circle cx="449" cy="336" r="7"/><circle cx="747" cy="336" r="7"/>
        <circle cx="782.7" cy="271" r="7"/><circle cx="1083.3" cy="271" r="7"/>
      </g>
    </svg>
    <div class="photo" role="img" aria-label="Photo of a cluttered storeroom before an estate clean-up" style="left:121px;top:152px;width:284px;height:284px;border-radius:50%;background:linear-gradient(150deg,#8a6a3e,#4a3b2c 50%,#9a8f82)"></div>
    <div class="photo" role="img" aria-label="Photo of a worker in a protective suit clearing pigeon waste in a roof space" style="left:456px;top:164px;width:284px;height:284px;border-radius:50%;background:linear-gradient(160deg,#555a52,#c7c9c4 55%,#6d6a5e)"></div>
    <div class="photo" role="img" aria-label="Photo of a fire-damaged kitchen" style="left:791px;top:152px;width:284px;height:284px;border-radius:50%;background:linear-gradient(160deg,#6e5f58,#2c2622 55%,#8a8580)"></div>
    <div class="svc-label" style="left:97px;top:487px">End of lease &amp; estate Clean ups Squalor Clean ups</div>
    <div class="svc-label" style="left:423px;top:487px">Pigeon Waste<br>Clean Ups</div>
    <div class="svc-label" style="left:763px;top:487px">Fire Damage<br>Clean Outs</div>
  </section>

  <h2 class="h2" style="left:108px;top:1856px;font-size:44px">Let's Get in Touch</h2>
  <p class="abs" style="left:111px;top:1932px;font-size:15px">We're open for any suggestion or just to have a chat.</p>
  <div class="info" style="top:1988px"><svg width="30" height="30" viewBox="0 0 30 30"><circle cx="15" cy="15" r="15" fill="#10c588"/><path d="M10 8l3 0 1.5 4-2 1.5a9 9 0 0 0 4 4l1.5-2 4 1.5v3a2 2 0 0 1-2 2A13 13 0 0 1 8 10a2 2 0 0 1 2-2z" fill="#fff"/></svg>Dennis or Arlo 0400 555 018</div>
  <div class="info" style="top:2032px"><svg width="30" height="30" viewBox="0 0 30 30"><circle cx="15" cy="15" r="15" fill="#10c588"/><rect x="8" y="10" width="14" height="10" rx="1" fill="#fff"/><path d="M8 10l7 6 7-6" fill="none" stroke="#10c588" stroke-width="1.5"/></svg>admin@korvaneservices.com</div>
  <div class="info" style="top:2075px"><svg width="30" height="30" viewBox="0 0 30 30"><path d="M15 2a10 10 0 0 0-10 10c0 8 10 16 10 16s10-8 10-16A10 10 0 0 0 15 2z" fill="#10c588"/><circle cx="15" cy="12" r="4" fill="#fff"/></svg>7B Orvell Avenue Fullarton SA 5063</div>

  <div class="field" style="top:1877px;height:49px"><svg width="20" height="20" viewBox="0 0 20 20"><circle cx="10" cy="6" r="4" fill="#666"/><path d="M2 19a8 8 0 0 1 16 0z" fill="#666"/></svg>Full Name</div>
  <div class="field" style="top:1948px;height:48px"><svg width="24" height="18" viewBox="0 0 24 18"><rect x="1" y="1" width="22" height="16" fill="none" stroke="#666" stroke-width="2"/><path d="M1 1l11 9 11-9" fill="none" stroke="#666" stroke-width="2"/></svg>Email</div>
  <div class="field" style="top:2020px;height:131px;align-items:flex-start;padding-top:14px"><svg width="22" height="20" viewBox="0 0 22 20" style="top:14px"><path d="M11 1C5 1 1 5 1 9c0 2 1 4 3 5l-1 5 5-3c1 0 2 .3 3 .3 6 0 10-4 10-8S17 1 11 1z" fill="#666"/></svg>Message</div>
  <a class="btn" style="left:644px;top:2177px;width:445px;height:49px;border-radius:0;font-size:17px">Send</a>

  <section class="quote" role="img" aria-label="Dark blue tinted photo of a cluttered workshop">
    <h2 class="abs" style="left:0;width:1200px;text-align:center;top:80px;font-size:44px;font-weight:700;color:#fff">Get a Quick Quote</h2>
    <p style="top:167px">Send a text to Korvane Services Please enter your mobile number or email and message</p>
    <p style="top:199px">Got more questions about our clean-up services and what we offer? Get in touch today <b style="font-size:19px">M 0400 555 018</b></p>
    <a class="btn" style="left:518px;top:259px;width:161px;height:45px;font-size:17px">Contact Us</a>
  </section>

  <h2 class="h2" style="left:0;width:1182px;text-align:center;top:2780px;font-size:44px">Testimonials</h2>
  <svg class="abs" style="left:50px;top:2974px" width="14" height="20" aria-hidden="true"><path d="M12 2L3 10l9 8" fill="none" stroke="#333" stroke-width="2.5"/></svg>
  <svg class="abs" style="left:1140px;top:2974px" width="14" height="20" aria-hidden="true"><path d="M2 2l9 8-9 8" fill="none" stroke="#333" stroke-width="2.5"/></svg>
  <div class="card" style="left:171px"><q>Dennis and his team arrived the next morning to clean up a rental property my husband and I own, which had been trashed by tenants. He was the only contractor to return my call. They did an amazing job and</q><div class="who"><b>Helena Marrow,</b><br>Satisfied Customer</div></div>
  <div class="card" style="left:702px"><q>We engaged Korvane Services to clean bird droppings from the facade of our commercial building. The job was so well done—it exceeded our expectations.</q><div class="who"><b>Tom Vellard,</b><br>Quellin Building Maintenance</div></div>
  <div class="mark" style="left:242px;top:2850px">“</div>
  <div class="mark" style="left:772px;top:2850px">“</div>
  <div class="avatar" role="img" aria-label="Customer portrait photo" style="left:110px;top:2937px;background:linear-gradient(160deg,#f3a9b4,#e98596)"></div>
  <div class="avatar" role="img" aria-label="Customer portrait photo" style="left:640px;top:2937px;background:linear-gradient(160deg,#e9ecef,#9fb6cc)"></div>

  <footer class="footer">
    <div class="abs" role="img" aria-label="Industry certification badge" style="left:110px;top:88px;width:84px;height:84px;border-radius:50%;background:radial-gradient(circle,#9fd26a,#2f8fc9)"></div>
    <div class="abs" style="left:205px;top:108px;width:130px;height:46px;border-radius:6px;background:#1e9fae"></div>
    <div class="abs" role="img" aria-label="Social profile" style="left:177px;top:210px;width:29px;height:29px;border-radius:50%;background:var(--green)"></div>
    <div class="abs" role="img" aria-label="Social profile" style="left:216px;top:210px;width:29px;height:29px;border-radius:50%;background:var(--white)"></div>

    <h3 class="fh" style="left:427px">Quick Links</h3>
    <ul class="flist" style="left:429px;top:124px">
      <li><span class="dot"></span>Home</li><li><span class="dot"></span>About</li><li><span class="dot"></span>Services</li><li><span class="dot"></span>Pricing</li><li><span class="dot"></span>Testimonials</li><li><span class="dot"></span>FAQ</li>
    </ul>
    <h3 class="fh" style="left:623px">Business Hours</h3>
    <ul class="flist" style="left:623px;top:124px">
      <li><svg width="22" height="22" viewBox="0 0 22 22"><circle cx="11" cy="11" r="11" fill="#10c588"/><path d="M11 5v6l4 3" stroke="#fff" stroke-width="2" fill="none"/></svg>Monday to Saturday</li>
      <li><svg width="22" height="22" viewBox="0 0 22 22"><circle cx="11" cy="11" r="11" fill="#10c588"/><path d="M11 5v6l4 3" stroke="#fff" stroke-width="2" fill="none"/></svg>8:00 am to 4:00 pm</li>
    </ul>
    <h3 class="fh" style="left:877px">Contact Us</h3>
    <ul class="flist" style="left:879px;top:126px">
      <li><svg width="22" height="22" viewBox="0 0 30 30"><circle cx="15" cy="15" r="15" fill="#10c588"/><path d="M10 8l3 0 1.5 4-2 1.5a9 9 0 0 0 4 4l1.5-2 4 1.5v3a2 2 0 0 1-2 2A13 13 0 0 1 8 10a2 2 0 0 1 2-2z" fill="#fff"/></svg>0400 555 018</li>
      <li><svg width="22" height="22" viewBox="0 0 30 30"><circle cx="15" cy="15" r="15" fill="#10c588"/><rect x="8" y="10" width="14" height="10" fill="#fff"/></svg>admin@korvaneservices.com</li>
      <li style="align-items:flex-start;height:auto;padding-top:4px"><svg width="22" height="24" viewBox="0 0 30 30"><path d="M15 2a10 10 0 0 0-10 10c0 8 10 16 10 16s10-8 10-16A10 10 0 0 0 15 2z" fill="#10c588"/><circle cx="15" cy="12" r="4" fill="#fff"/></svg><span style="line-height:27px">7B Orvell Avenue<br>Fullarton SA 5063</span></li>
    </ul>
    <div class="abs" style="left:110px;top:322px;width:980px;height:1px;background:#4b6380"></div>
    <p class="abs" style="left:0;width:1200px;text-align:center;top:338px;font-size:15px;color:#fff">Copyright © 2025 Korvane. All rights reserved.</p>
  </footer>
</div>
</body>
</html>
```